International Clinical Software Company needs a new business card design

We are looking for a new business card design for our company that has recently expanded into the UK market, making us a multinational company.
After having rebranded our website and produced a new style guide, we are looking for a business card that is creative and attention grabbing, while being consistent with the style and colour scheme used on the new website, www.plumvora.example
We produce care management technology for the aged care market, but the main aspect we aim to communicate is the human element of our software, and the way it assists in providing better care for aged people, and stronger relationships between aged people and the staff that care for them.
Our current business card is a dark green with gold text, which makes the text quite difficult to read, not very aesthetically appealing and the colour scheme looks quite dated.
We would like something fresh and modern, that can still be colourful but doesn't use large blocks of dark colour, and uses the colours within our logo.
Something tying in with the leaves that are used in our logo could work quite nicely, along with the Autumn/Fall colours of soft greens, yellows and reds (also in our existing logo). However also happy to look at fresh, completely out of the box ideas we may not have yet considered.
Target Market(s)
The people that receive this business card work in the aged card or health industry and are either corporate/management level staff or clinical (Registered Nurses, care workers etc.)
Industry/Entity Type
Health Product
Contact Information for Business Card
Company Name - BrindlewayCare
Company locations: Northvale, Eastmere, Southhaven
Staff Details:
Staff name: Derek Mallow
Staff job title: Executive Chairman
Staff email: d.mallow@plumvora.example
Office phone number: 01742 918576
Font styles to use
Other font styles liked:
- Calibri
Requirements
Must have
- Must include the BrindlewayCare brand name in it's current font
- Must include logo (3 leaves in gold circle)
- Must include Business Card Details
Nice to have
- Elements of gold
- White space
- Something autumn themed but not too cliched
Should not have
- No blue - used by a major competitor and we would like to differentiate from them
- Large blocks of dark green colour (the green that appears in our leaves on the logo on our current business card is the background colour and it is far too dark)

```html
<!DOCTYPE html>
<html lang="en">
<head>
<meta charset="utf-8">
<title>BrindlewayCare Business Card</title>
<link rel="stylesheet" href="https://fonts.googleapis.com/css2?family=Open+Sans:wght@300;400;600&display=swap">
<style>
  :root {
    --page: #ecebe8;
    --card: #ffffff;
    --gold: #b39a6a;
    --ink: #2b2b2b;
    --icon: #a8905f;
    --leaf-wash-a: rgba(238, 222, 204, 0.55);
    --leaf-wash-b: rgba(246, 236, 225, 0.25);
    --leaf-green: #5a7a32;
    --leaf-gold: #c9b24a;
    --leaf-red: #cf4450;
  }
  * { box-sizing: border-box; margin: 0; padding: 0; }
  html, body {
    width: 1200px; height: 900px; overflow: hidden;
    background: var(--page);
    font-family: "Open Sans", Calibri, sans-serif;
  }
  .business-card {
    position: absolute; left: 100px; top: 164px;
    width: 1000px; height: 572px;
    background: var(--card);
    border-radius: 34px;
    overflow: hidden;
    box-shadow: 0 10px 30px rgba(0,0,0,0.12);
  }
  .autumn-wash {
    position: absolute; left: 300px; top: 0; width: 700px; height: 572px;
    background: radial-gradient(ellipse at 60% 40%, var(--leaf-wash-a), var(--leaf-wash-b) 60%, transparent 85%);
  }
  .leaf-corner {
    position: absolute; left: 0; bottom: 0; width: 300px; height: 190px;
    background: linear-gradient(160deg, transparent 25%, var(--leaf-green) 45%, var(--leaf-gold) 65%, var(--leaf-red) 85%);
    clip-path: polygon(0 55%, 100% 100%, 0 100%);
    opacity: 0.9;
  }
  .brand-vertical {
    position: absolute; left: 78px; top: 290px;
    transform: translate(-50%, -50%) rotate(-90deg);
    font-weight: 300; font-size: 44px; letter-spacing: 1px;
    color: var(--gold); white-space: nowrap;
  }
  .brand-mark {
    position: absolute; left: 430px; top: 70px;
    display: flex; align-items: center; gap: 14px;
  }
  .brand-mark .dot {
    width: 64px; height: 64px; border-radius: 50%;
    border: 3px solid var(--gold);
  }
  .brand-mark .name {
    font-weight: 400; font-size: 30px; color: var(--gold);
  }
  .person {
    position: absolute; left: 430px; top: 232px;
  }
  .person .full-name {
    font-size: 32px; font-weight: 400; color: var(--gold); line-height: 1.1;
  }
  .person .job-title {
    font-size: 18px; font-weight: 400; color: var(--ink); margin-top: 4px;
  }
  .contact-list {
    position: absolute; left: 460px; top: 334px;
    list-style: none; font-size: 19px; color: var(--ink); line-height: 1.3;
  }
  .contact-list li { display: flex; align-items: flex-start; gap: 12px; margin-bottom: 4px; }
  .contact-list svg { width: 20px; height: 20px; flex: none; margin-top: 3px; fill: var(--icon); }
</style>
</head>
<body>
  <main class="business-card">
    <div class="autumn-wash" role="img" aria-label="Faint photograph of autumn leaves on branches"></div>
    <div class="leaf-corner" role="img" aria-label="Illustration of green, gold and red leaves in the corner"></div>

    <div class="brand-vertical">BrindlewayCare</div>

    <div class="brand-mark">
      <span class="dot"></span>
      <span class="name">BrindlewayCare</span>
    </div>

    <section class="person">
      <h1 class="full-name">Derek Mallow</h1>
      <p class="job-title">Executive Chairman</p>
    </section>

    <ul class="contact-list">
      <li>
        <svg viewBox="0 0 24 24" aria-hidden="true"><path d="M3 8c0-2 2-4 9-4s9 2 9 4v2h-5V8H8v2H3z M6 11h12l2 9H4z M12 13a3 3 0 1 0 0 6 3 3 0 0 0 0-6z"/></svg>
        <span>01742 918576</span>
      </li>
      <li>
        <svg viewBox="0 0 24 24" aria-hidden="true"><path d="M2 5h20v14H2z M3 6l9 7 9-7v1l-9 7-9-7z" fill-rule="evenodd"/></svg>
        <span>d.mallow@plumvora.example</span>
      </li>
      <li>
        <svg viewBox="0 0 24 24" aria-hidden="true"><path d="M12 3l10 9h-3v9h-5v-6h-4v6H5v-9H2z"/></svg>
        <span>BrindlewayCare<br>Northvale, Eastmere, Southhaven</span>
      </li>
    </ul>
  </main>
</body>
</html>
```